Stonebrace Business Card Design

The Stonebrace Co is an aggregate (crushing) equipment dealer serving Western Canadian provinces. Stonebrace is a distributor of aggregate equipment for different manufacturers.

We are looking to change and update the existing business card which has been used since the existence of the company. A copy of existing card has been attached for reference. The Stonebrace Co logo we want to remain the same and we want the green color to remain the same.

We are wanting something new with a different look. A refreshing card to show a new modern and updated look. No longer wanting to have the manufacturers on the back of the card but something more like our logo on the back of the card with a statement like "Crushing Solutions"

ideas could be:
- card can be different colors on front and back
- front or reverse of the card could possibly be the green color with the logo in black

Target Market(s)

Owners of Aggregate/Crushing companies

Contact Information for Business Card

see above

Requirements
Must have
• - logo to remain same along with same font within logo
• - green color to remain same
Nice to have
• as noted above under project description
Should not have

```html
<!DOCTYPE html>
<html lang="en">
<head>
<meta charset="utf-8">
<title>Stonebrace Business Card</title>
<link href="https://fonts.googleapis.com/css2?family=Roboto:wght@400;500;700&display=swap" rel="stylesheet">
<style>
  :root {
    --brand-green: #868a0b;
    --brand-green-dark: #767a08;
    --ink: #1f1f1f;
    --text-grey: #555555;
    --card-white: #f4f4f2;
    --backdrop: #e6e4df;
  }
  * { margin: 0; padding: 0; box-sizing: border-box; }
  html, body {
    width: 1200px; height: 960px; overflow: hidden;
    background: var(--backdrop);
    font-family: "Roboto", Arial, sans-serif;
  }
  .canvas { position: relative; width: 1200px; height: 960px; }

  .card {
    position: absolute; left: 320px; width: 600px;
    border-radius: 18px; overflow: hidden;
  }

  /* Front: green with black wordmark */
  .card--front {
    top: 95px; height: 355px;
    background: var(--brand-green);
  }
  .card--front .mark {
    position: absolute; left: 133px; top: 157px;
    width: 56px; height: 56px; border-radius: 50%;
    background: var(--ink);
  }
  .card--front .wordmark {
    position: absolute; left: 249px; top: 172px;
    font-size: 23px; font-weight: 700; color: var(--ink);
    letter-spacing: 0.2px; white-space: nowrap;
  }
  .card--front .tagline {
    position: absolute; left: 0; right: 0; top: 304px;
    text-align: center; font-size: 15px; font-weight: 500; color: var(--ink);
  }

  /* Back: white with contact details */
  .card--back {
    top: 493px; height: 342px;
    background: var(--card-white);
  }
  .card--back .swoosh { position: absolute; inset: 0; }
  .card--back .mark {
    position: absolute; left: 110px; top: 27px;
    width: 90px; height: 90px; border-radius: 50%;
    background: var(--brand-green);
  }
  .card--back .wordmark {
    position: absolute; left: 30px; top: 137px;
    font-size: 21px; font-weight: 700; color: var(--ink);
    letter-spacing: 0.2px; white-space: nowrap;
  }
  .address {
    position: absolute; left: 25px; top: 178px;
    font-size: 14px; line-height: 19px; color: var(--text-grey); font-style: normal;
  }
  .contact-list {
    position: absolute; left: 25px; top: 225px; list-style: none;
  }
  .contact-list li {
    display: flex; align-items: center; gap: 9px;
    font-size: 14px; line-height: 19px; color: var(--text-grey);
  }
  .contact-list svg { width: 13px; height: 13px; fill: var(--brand-green); flex: none; }
  .person {
    position: absolute; right: 36px; top: 277px; text-align: right;
  }
  .person-name { font-size: 20px; font-weight: 700; color: var(--brand-green); line-height: 24px; }
  .person-role { font-size: 14px; font-weight: 500; color: var(--ink); line-height: 20px; }
</style>
</head>
<body>
<main class="canvas">

  <section class="card card--front" aria-label="Card front">
    <span class="mark"></span>
    <div class="wordmark">THE STONEBRACE CO.</div>
    <div class="tagline">Crushing Solutions</div>
  </section>

  <section class="card card--back" aria-label="Card back">
    <svg class="swoosh" viewBox="0 0 600 342" width="600" height="342" aria-hidden="true">
      <path d="M375,0 C485,40 585,135 593,268 C583,150 505,60 408,0 Z" fill="var(--brand-green)"/>
      <path d="M425,0 H600 V212 C575,120 520,50 425,0 Z" fill="var(--brand-green)"/>
    </svg>
    <span class="mark"></span>
    <div class="wordmark">THE STONEBRACE CO.</div>
    <address class="address">2210- 48B Avenue<br>Nisku, Alberta T9E 1K7</address>
    <ul class="contact-list">
      <li><svg viewBox="0 0 16 16"><path d="M3 1l3 0 1.5 4-2 1.5c1 2 2.5 3.5 4.5 4.5L11.5 9l4 1.5v3c0 1-1 1.5-2 1.5C7 15 1 9 1 3c0-1 .5-2 2-2z"/></svg>780.555.0142</li>
      <li><svg viewBox="0 0 16 16"><path d="M4 0h8a1 1 0 0 1 1 1v14a1 1 0 0 1-1 1H4a1 1 0 0 1-1-1V1a1 1 0 0 1 1-1zm1 2v10h6V2zm3 11a1 1 0 1 0 0 2 1 1 0 0 0 0-2z"/></svg>780.555.0187</li>
      <li><svg viewBox="0 0 16 16"><path d="M4 1h8v4H4zM1 6h14v6h-2v-2H3v2H1zM4 11h8v4H4z"/></svg>780.555.0163</li>
      <li><svg viewBox="0 0 16 16"><path d="M1 3h14v1L8 9 1 4zM1 6l7 5 7-5v7H1z"/></svg>dale@stonebr.com</li>
      <li><svg viewBox="0 0 16 16"><path d="M8 0a8 8 0 1 0 0 16A8 8 0 0 0 8 0zm-1 2v2L5 6H3a5 5 0 0 1 4-4zm2 0a6 6 0 0 1 4.5 9H11l-1-2 1-2-2-2zM3 8h2l2 2v4a6 6 0 0 1-4-6z"/></svg>www.stonebrace.ca</li>
    </ul>
    <div class="person">
      <div class="person-name">DALE MARCHUK</div>
      <div class="person-role">CEO/FOUNDER</div>
    </div>
  </section>

</main>
</body>
</html>
```